Design a web site for my business - Brightline Coatings Co.

We are a family business that handles design, fabrication and installation of powder coated aluminum, stainless steel and glass products. Including handrails, privacy slat screens, electric gates and pool fencing. We are based in the Whitsundays in North Queensland and service an area from Airlie Beach to Townsville.

Target Market(s)

Domestic and commercial

Industry/Entity Type

fabrication - manufacturing

Coding

Coded - Design and coding required

Number of Pages Required

5+ page

Colors
0054AA
0677BA
7BADD7
CADEEF
E8F1F8

Requirements
Must have
• photo galleries, contact page, one page for privacy screens, balustrades, glass fencing, stainless steel handrail, powder coated aluminium handrails and pool fencing

```html
<!DOCTYPE html>
<html lang="en">
<head>
<meta charset="utf-8">
<title>Brightline Coatings Co — Aluminium, Stainless Steel &amp; Glass</title>
<link href="https://fonts.googleapis.com/css2?family=Bebas+Neue&family=Montserrat:wght@400;500;600;700&display=swap" rel="stylesheet">
<style>
:root{
  --blue-deep:#0054AA;
  --blue:#0677BA;
  --blue-mid:#7BADD7;
  --blue-soft:#CADEEF;
  --blue-pale:#E8F1F8;
  --navy:#0a2342;
  --navy-2:#0d2c52;
  --card:#f5f9fd;
  --text:#1c2a3a;
  --muted:#5d6b7a;
  --white:#ffffff;
}
*{box-sizing:border-box;margin:0;padding:0}
html,body{width:1200px;height:5141px;overflow:hidden}
body{font-family:"Montserrat",sans-serif;color:var(--text);background:var(--blue-pale);position:relative}
.display{font-family:"Bebas Neue",sans-serif;font-weight:400;letter-spacing:.5px;line-height:.95}
.eyebrow{font-size:13px;letter-spacing:2px;color:var(--blue);text-transform:uppercase;font-weight:500}
.on-dark .eyebrow{color:var(--blue-mid)}
.rule{width:90px;height:3px;background:var(--blue);margin:14px auto 0}
.on-dark .rule{background:var(--blue-mid)}
.btn{display:inline-flex;align-items:center;gap:6px;background:linear-gradient(180deg,var(--blue),var(--blue-deep));color:var(--white);font-size:12px;font-weight:700;letter-spacing:.5px;text-transform:uppercase;padding:0 26px;height:46px;border-radius:3px;text-decoration:none;white-space:nowrap}
.btn-outline{background:transparent;border:1px solid rgba(255,255,255,.75)}
.btn-dark{background:var(--navy)}
.ph{display:block}
section{position:absolute;left:0;width:1200px}

/* hero */
.hero{top:0;height:686px;color:var(--white)}
.hero-photo{position:absolute;inset:0}
.hero-shade{position:absolute;inset:0;background:linear-gradient(90deg,rgba(6,22,44,.82) 0%,rgba(6,22,44,.4) 55%,rgba(6,22,44,.1) 100%)}
.nav{position:absolute;top:20px;left:128px;right:102px;display:flex;align-items:center;height:42px}
.brand{display:flex;align-items:center;gap:10px;font-weight:700;font-size:18px;letter-spacing:.3px;color:var(--white);white-space:nowrap}
.brand-mark{width:26px;height:26px;border:2px solid var(--blue-mid)}
.nav-links{display:flex;gap:40px;margin-left:46px;font-size:11px;font-weight:600;text-transform:uppercase;white-space:nowrap}
.nav .btn{margin-left:auto;height:40px;padding:0 24px;font-size:11px}
.hero-copy{position:absolute;left:116px;top:178px;width:520px}
.hero .eyebrow{color:var(--blue-mid)}
.hero h1{font-size:58px;margin:10px 0 14px}
.hero p{font-size:12.5px;line-height:1.45;max-width:420px}
.hero-ctas{display:flex;gap:12px;margin-top:26px}
.badges{display:flex;gap:34px;margin-top:40px}
.badge{display:flex;align-items:center;gap:10px;font-size:10px;font-weight:700;text-transform:uppercase;line-height:1.3}
.badge svg{width:22px;height:22px;stroke:var(--blue-mid);fill:none;stroke-width:1.6;flex:none}

/* services */
.services{top:686px;height:946px;background:var(--blue-pale);text-align:center}
.services .eyebrow{margin-top:56px}
.services h2{font-size:50px;margin-top:10px;color:var(--navy)}
.grid{position:absolute;display:flex;gap:10px}
.row1{top:238px;left:57px}
.row2{top:580px;left:170px}
.card{width:265px;background:var(--card);text-align:left;border-bottom:3px solid var(--blue-soft)}
.row2 .card{width:271px}
.card .ph{height:195px}
.row2 .card .ph{height:150px}
.card-body{display:flex;gap:14px;padding:18px 14px 14px}
.card h3{font-family:"Bebas Neue",sans-serif;font-weight:400;font-size:21px;color:var(--navy)}
.card p{font-size:9.5px;line-height:1.55;color:var(--muted);margin-top:4px}
.explore{font-size:9px;font-weight:700;color:var(--blue);letter-spacing:1px;margin-top:8px;display:block}
.icon{flex:none;width:36px;height:36px;stroke:var(--blue);fill:none;stroke-width:1.6}

/* about */
.about{top:1632px;height:598px;background:var(--navy);color:var(--white)}
.about-photo{position:absolute;left:0;top:0;width:580px;height:598px}
.play{position:absolute;left:262px;top:232px;width:72px;height:72px;border-radius:50%;border:3px solid var(--white);background:rgba(0,0,0,.25)}
.play::after{content:"";position:absolute;left:28px;top:21px;border-left:22px solid var(--white);border-top:14px solid transparent;border-bottom:14px solid transparent}
.about-copy{position:absolute;left:676px;top:102px;width:450px}
.about h2{font-size:50px;margin:12px 0 0}
.about .rule{margin:16px 0 22px}
.about p{font-size:13.5px;line-height:1.85;margin-bottom:10px}
.stats{display:flex;margin-top:26px}
.stat{padding-right:36px}
.stat + .stat{border-left:1px solid var(--blue-mid);padding-left:36px}
.stat b{font-family:"Bebas Neue",sans-serif;font-weight:400;font-size:40px;color:var(--blue-mid);display:block}
.stat span{font-size:11px;font-weight:600;text-transform:uppercase}

/* process */
.process{top:2230px;height:780px;background:var(--blue-pale)}
.process-copy{position:absolute;left:128px;top:82px;width:470px}
.process h2{font-size:54px;color:var(--navy);margin-top:10px}
.process .lead{font-size:14px;line-height:1.8;margin-top:34px}
.steps{margin-top:30px}
.step{display:flex;align-items:flex-start;gap:14px;height:74px}
.step .num{font-size:18px;color:var(--blue);width:30px;margin-top:6px}
.step h4{font-size:17px;font-weight:500;color:var(--navy)}
.step p{font-size:12.5px;color:var(--muted);margin-top:4px}
.process .btn{margin-top:22px;height:56px;padding:0 44px}
.hexes{position:absolute;left:590px;top:80px}

/* testimonials */
.testimonials{top:3010px;height:600px;background:var(--navy);color:var(--white);text-align:center}
.testimonials .eyebrow{margin-top:48px;font-size:12px}
.testimonials h2{font-size:54px;margin-top:6px}
.quotes{position:absolute;top:170px;left:127px;display:flex;gap:18px}
.quote{width:464px;height:270px;border:1px solid var(--blue-mid);padding:34px 44px 0}
.quote p{font-size:18px;line-height:1.6;margin-top:12px}
.stars{color:var(--blue-mid);font-size:20px;letter-spacing:2px;margin-top:6px;line-height:1}
.quote b{font-size:13px;display:block}
.arrow{position:absolute;top:292px}
.testimonials .btn{position:absolute;left:489px;top:468px;height:52px;padding:0 36px}

/* areas */
.areas{top:3610px;height:640px;background:var(--blue-pale)}
.areas h2{font-size:54px;text-align:center;margin-top:56px;color:var(--navy)}
.areas-panel{position:absolute;top:158px;left:107px;width:1014px;height:412px;display:flex;background:var(--white)}
.areas-list{width:506px;padding:44px 0 0 82px}
.areas-list h3{font-family:"Bebas Neue",sans-serif;font-weight:400;font-size:36px;color:var(--navy)}
.areas-list ul{list-style:none;width:344px;margin-top:14px}
.areas-list li{display:flex;align-items:center;gap:16px;font-size:19px;height:42px;border-bottom:1px solid var(--blue-soft);padding-left:16px}
.areas-list .btn{margin-top:26px;height:40px;font-size:10px;padding:0 30px}
.map{width:508px;height:412px}

/* cta */
.cta{top:4250px;height:485px;background:linear-gradient(90deg,var(--blue-mid) 0%,var(--blue) 45%,var(--blue-deep) 100%)}
.cta-photo{position:absolute;left:0;top:0;width:560px;height:485px}
.cta-copy{position:absolute;left:602px;top:118px;width:540px;color:var(--white)}
.cta .eyebrow{color:var(--white)}
.cta h2{font-size:50px;margin-top:12px;white-space:nowrap}
.cta p{font-size:16px;line-height:1.55;margin-top:16px;max-width:470px}
.cta .btn{margin-top:26px;height:52px;padding:0 36px}

/* footer */
footer{position:absolute;top:4735px;left:0;width:1200px;height:406px;background:var(--navy);color:#e3ecf5}
.foot-cols{position:absolute;top:60px;left:128px;display:flex}
.foot-brand{width:292px}
.foot-brand .brand{font-size:19px}
.foot-brand p{font-size:9.5px;line-height:1.75;margin-top:16px;color:#b4c5d8;width:236px}
.socials{display:flex;gap:6px;margin-top:12px}
.socials span{width:22px;height:22px;border-radius:50%;background:var(--white)}
.foot-col{border-left:2px solid var(--blue-mid);padding-left:10px}
.foot-col h5{font-family:"Bebas Neue",sans-serif;font-weight:400;font-size:19px;color:var(--white)}
.foot-col ul{list-style:none;margin-top:12px;padding-left:4px}
.foot-col li{font-size:10.5px;line-height:1.85;color:#c9d7e6;white-space:nowrap}
.contact-row{display:flex;gap:10px;font-size:10px;margin-top:12px;padding-left:4px;line-height:1.5}
.contact-row svg{flex:none;width:14px;height:14px;fill:var(--blue-mid)}
.foot-bottom{position:absolute;left:128px;right:108px;top:370px;display:flex;justify-content:space-between;font-size:10px;color:#9fb3c9}
</style>
</head>
<body>

<section class="hero on-dark">
  <svg class="ph hero-photo" role="img" aria-label="Modern home at dusk with a black aluminium slat sliding gate and glass balcony" width="1200" height="686">
    <defs><linearGradient id="heroSky" x1="0" y1="0" x2="1" y2="1"><stop offset="0" stop-color="#2f3d52"/><stop offset=".45" stop-color="#5b5a5e"/><stop offset=".75" stop-color="#242a33"/><stop offset="1" stop-color="#12161c"/></linearGradient></defs>
    <rect width="1200" height="686" fill="url(#heroSky)"/>
  </svg>
  <div class="hero-shade"></div>
  <nav class="nav">
    <div class="brand"><span class="brand-mark"></span>Brightline Coatings Co</div>
    <div class="nav-links"><span>About</span><span>Services</span><span>Gallery</span><span>Areas We Service</span><span>Contact</span></div>
    <a class="btn">Get a Quote ↗</a>
  </nav>
  <div class="hero-copy">
    <div class="eyebrow">Your Business Name</div>
    <h1 class="display">Quality Aluminium,<br>Stainless Steel &amp;<br>Glass Solutions</h1>
    <p>From concept to completion, we design, fabricate and install premium powder coated aluminium, stainless steel and glass products</p>
    <div class="hero-ctas">
      <a class="btn">Get a Free Quote ↗</a>
      <a class="btn btn-outline"><svg width="14" height="14" viewBox="0 0 24 24" fill="#fff"><path d="M6.6 10.8a15.1 15.1 0 0 0 6.6 6.6l2.2-2.2a1 1 0 0 1 1-.25 11.4 11.4 0 0 0 3.6.57 1 1 0 0 1 1 1V20a1 1 0 0 1-1 1A17 17 0 0 1 3 4a1 1 0 0 1 1-1h3.5a1 1 0 0 1 1 1c0 1.25.2 2.45.57 3.6a1 1 0 0 1-.25 1z"/></svg>Call 0400 000 111</a>
    </div>
    <div class="badges">
      <div class="badge"><svg viewBox="0 0 24 24"><circle cx="8" cy="7" r="3"/><circle cx="16" cy="7" r="3"/><path d="M3 20v-4a4 4 0 0 1 4-4h2a4 4 0 0 1 4 4v4M13 20v-3a4 4 0 0 1 4-4 4 4 0 0 1 4 4v3"/></svg>Family Owned<br>&amp; Operated</div>
      <div class="badge"><svg viewBox="0 0 24 24"><circle cx="12" cy="9" r="6"/><path d="M8 14l-2 8 6-3 6 3-2-8"/></svg>Quality<br>Workmanship</div>
      <div class="badge"><svg viewBox="0 0 24 24" style="fill:var(--blue-mid);stroke:none"><path d="M3 10l4-4 4 1 3-3 3 2 2 5 2 3-2 5-5 1-3-2-4 1-3-3z"/></svg>Built to Austrlian<br>Standard</div>
    </div>
  </div>
</section>

<section class="services">
  <div class="eyebrow">Our Services</div>
  <h2 class="display">Complete Design, Fabrication<br>&amp; Installation Services</h2>
  <div class="rule"></div>

  <div class="grid row1">
    <article class="card">
      <svg class="ph" role="img" aria-label="Interior staircase with glass and steel handrail" width="265" height="195"><rect width="265" height="195" fill="#d9d8d4"/></svg>
      <div class="card-body"><svg class="icon" viewBox="0 0 36 36"><path d="M4 32h8v-7h7v-7h7v-7h6M6 24L28 6"/></svg><div><h3>Handrails</h3><p>Safe, stylish and built to last. Custom handrails in aluminium, stainless steel and glass.</p><span class="explore">EXPLORE →</span></div></div>
    </article>
    <article class="card">
      <svg class="ph" role="img" aria-label="Black slat electric driveway gate in tropical garden" width="265" height="195"><rect width="265" height="195" fill="#5f7566"/></svg>
      <div class="card-body"><svg class="icon" viewBox="0 0 36 36"><rect x="4" y="8" width="28" height="22"/><path d="M10 8v22M16 8v22M22 8v22M28 8v22"/></svg><div><h3>Electric Gates</h3><p>Automatic gates designed for security, convenience and peace of mind.</p><span class="explore">EXPLORE →</span></div></div>
    </article>
    <article class="card">
      <svg class="ph" role="img" aria-label="Dark aluminium privacy slat screen with plants" width="265" height="195"><rect width="265" height="195" fill="#3c4436"/></svg>
      <div class="card-body"><svg class="icon" viewBox="0 0 36 36"><rect x="4" y="6" width="28" height="24"/><path d="M4 12h28M4 18h28M4 24h28"/></svg><div><h3>Privacy Screens</h3><p>Sleek aluminium slat screens for privacy, shade and architectural style.</p><span class="explore">EXPLORE →</span></div></div>
    </article>
    <article class="card">
      <svg class="ph" role="img" aria-label="Infinity pool with glass fencing overlooking the ocean" width="265" height="195"><rect width="265" height="195" fill="#3f8fae"/></svg>
      <div class="card-body"><svg class="icon" viewBox="0 0 36 36"><path d="M4 30h28M8 30V8M28 30V8M8 12h20M8 24h20M14 12v12M22 12v12"/></svg><div><h3>Pool Fencing</h3><p>Beautiful, compliant pool fencing that enhances your space and protects your family.</p><span class="explore">EXPLORE →</span></div></div>
    </article>
  </div>

  <div class="grid row2">
    <article class="card">
      <svg class="ph" role="img" aria-label="Glass balustrade balcony overlooking islands" width="271" height="150"><rect width="271" height="150" fill="#4d86a0"/></svg>
      <div class="card-body"><svg class="icon" viewBox="0 0 36 36"><path d="M4 8h28M6 8v24M30 8v24M12 12h12v16H12z"/></svg><div><h3>Glass Balustrades</h3><p>Frameless and semi-frameless glass balustrades for uninterrupted views and luxury finishes.</p><span class="explore">EXPLORE →</span></div></div>
    </article>
    <article class="card">
      <svg class="ph" role="img" aria-label="Stainless steel wire balustrade at sunset by the sea" width="271" height="150"><rect width="271" height="150" fill="#8a8480"/></svg>
      <div class="card-body"><svg class="icon" viewBox="0 0 36 36"><path d="M6 30l10-10M14 22l8-8M20 10a6 6 0 1 1 6 6l-4 4-6-6z"/></svg><div><h3>Stainless Steel</h3><p>Corrosion resistant and built for strength in coastal environments.</p><span class="explore">EXPLORE →</span></div></div>
    </article>
    <article class="card">
      <svg class="ph" role="img" aria-label="Welder fabricating aluminium in the workshop" width="271" height="150"><rect width="271" height="150" fill="#3a4047"/></svg>
      <div class="card-body"><svg class="icon" viewBox="0 0 36 36"><path d="M8 10a10 10 0 0 1 20 0v8H8zM12 18v6h12v-6M16 24v6"/></svg><div><h3>Aluminium Fabrication</h3><p>Custom fabricated aluminium solutions and architectural features made in-house.</p><span class="explore">EXPLORE →</span></div></div>
    </article>
  </div>
</section>

<section class="about on-dark">
  <svg class="ph about-photo" role="img" aria-label="Installer fitting a black slat gate outside a modern home" width="580" height="598"><defs><linearGradient id="aboutG" x1="0" y1="0" x2="1" y2="1"><stop offset="0" stop-color="#8b8f8a"/><stop offset=".5" stop-color="#5b6a4c"/><stop offset="1" stop-color="#a79f92"/></linearGradient></defs><rect width="580" height="598" fill="url(#aboutG)"/></svg>
  <div class="play"></div>
  <div class="about-copy">
    <div class="eyebrow">About Company</div>
    <h2 class="display">Family Owned.<br>Quality Focused</h2>
    <div class="rule"></div>
    <p>As a locally owned family business, we take pride in delivering high-quality metal and glass solutions that are built to perform and designed to complement your property.</p>
    <p>From the initial design consultation through fabrication and professional installation, every project is completed</p>
    <div class="stats">
      <div class="stat"><b>20+</b><span>Years of Experience</span></div>
      <div class="stat"><b>1000+</b><span>Thousands of Installations</span></div>
    </div>
  </div>
</section>

<section class="process">
  <div class="process-copy">
    <div class="eyebrow">How We Work</div>
    <h2 class="display">Our Process</h2>
    <p class="lead">From the initial design consultation through fabrication and professional installation, every project</p>
    <div class="steps">
      <div class="step"><svg class="icon" viewBox="0 0 36 36"><path d="M6 6l24 24M30 6L6 30M4 4h6v6M26 26h6v6"/></svg><span class="num">01</span><div><h4>Design</h4><p>Lorem ipsum dolor sit amet consectetur adipiscing</p></div></div>
      <div class="step"><svg class="icon" viewBox="0 0 36 36"><path d="M4 30h28M8 26h20M10 6l14 14-4 4L6 10z"/></svg><span class="num">02</span><div><h4>Fabrication</h4><p>Lorem ipsum dolor sit amet consectetur adipis</p></div></div>
      <div class="step"><svg class="icon" viewBox="0 0 36 36"><path d="M6 10h14v8H6zM20 14h6M12 18l-2 12M28 10l2-2M28 14h4M28 18l2 2"/></svg><span class="num">03</span><div><h4>Powder Coating</h4><p>Lorem ipsum dolor sit amet consectetur adipiscing</p></div></div>
      <div class="step"><svg class="icon" viewBox="0 0 36 36"><path d="M6 30l14-14M22 6a6 6 0 0 0 6 10l-4 4M8 6l8 8M30 30l-8-8"/></svg><span class="num">04</span><div><h4>Installation</h4><p>Lorem ipsum dolor sit amet consectetur adipi</p></div></div>
    </div>
    <a class="btn">Get a Free Quote ↗</a>
  </div>
  <svg class="hexes" role="img" aria-label="Hexagon photo collage of a coastal home with gate and sparks from metal cutting" width="560" height="640" viewBox="0 0 560 640">
    <defs>
      <linearGradient id="hexSea" x1="0" y1="0" x2="0" y2="1"><stop offset="0" stop-color="#a9c6dc"/><stop offset=".5" stop-color="#2f7f98"/><stop offset="1" stop-color="#4d5a52"/></linearGradient>
      <radialGradient id="hexSpark" cx=".5" cy=".4" r=".6"><stop offset="0" stop-color="#f0a24a"/><stop offset=".5" stop-color="#9a4a1a"/><stop offset="1" stop-color="#2a1a12"/></radialGradient>
    </defs>
    <polygon points="304,0 540,130 540,440 304,565 67,440 67,130" fill="url(#hexSea)"/>
    <polygon points="145,330 265,400 265,540 145,610 25,540 25,400" fill="url(#hexSpark)" stroke="#E8F1F8" stroke-width="8"/>
  </svg>
</section>

<section class="testimonials on-dark">
  <div class="eyebrow">Reviews</div>
  <h2 class="display">Testimonials</h2>
  <div class="rule"></div>
  <svg class="arrow" style="left:84px" width="24" height="40" viewBox="0 0 24 40"><path d="M20 2L4 20l16 18" stroke="#7BADD7" stroke-width="3" fill="none"/></svg>
  <svg class="arrow" style="left:1092px" width="24" height="40" viewBox="0 0 24 40"><path d="M4 2l16 18L4 38" stroke="#7BADD7" stroke-width="3" fill="none"/></svg>
  <div class="quotes">
    <div class="quote">
      <svg width="42" height="28" viewBox="0 0 42 28" fill="#7BADD7"><path d="M0 0h18v16l-8 12H4l6-12H0zM24 0h18v16l-8 12h-6l6-12h-10z"/></svg>
      <p>"The workmanship was outstanding from start to finish. Our new electric gate and privacy screens have completely transformed our home."</p>
      <div class="stars">★★★★★</div><b>Customer Name</b>
    </div>
    <div class="quote">
      <svg width="42" height="28" viewBox="0 0 42 28" fill="#7BADD7"><path d="M0 0h18v16l-8 12H4l6-12H0zM24 0h18v16l-8 12h-6l6-12h-10z"/></svg>
      <p>"The workmanship was outstanding from start to finish. Our new electric gate and privacy screens have completely transformed our home."</p>
      <div class="stars">★★★★★</div><b>Customer Name</b>
    </div>
  </div>
  <a class="btn">Get a Free Quote ↗</a>
</section>

<section class="areas">
  <h2 class="display">Service Areas</h2>
  <div class="areas-panel">
    <div class="areas-list">
      <h3>Areas We Service</h3>
      <ul>
        <li><svg width="12" height="16" viewBox="0 0 12 16" fill="#0677BA"><path d="M6 0a6 6 0 0 1 6 6c0 4-6 10-6 10S0 10 0 6a6 6 0 0 1 6-6z"/></svg>Whitsundays</li>
        <li><svg width="12" height="16" viewBox="0 0 12 16" fill="#0677BA"><path d="M6 0a6 6 0 0 1 6 6c0 4-6 10-6 10S0 10 0 6a6 6 0 0 1 6-6z"/></svg>Airlie Beach</li>
        <li><svg width="12" height="16" viewBox="0 0 12 16" fill="#0677BA"><path d="M6 0a6 6 0 0 1 6 6c0 4-6 10-6 10S0 10 0 6a6 6 0 0 1 6-6z"/></svg>Bowen</li>
        <li><svg width="12" height="16" viewBox="0 0 12 16" fill="#0677BA"><path d="M6 0a6 6 0 0 1 6 6c0 4-6 10-6 10S0 10 0 6a6 6 0 0 1 6-6z"/></svg>Ayr</li>
        <li style="border:none"><svg width="12" height="16" viewBox="0 0 12 16" fill="#0677BA"><path d="M6 0a6 6 0 0 1 6 6c0 4-6 10-6 10S0 10 0 6a6 6 0 0 1 6-6z"/></svg>Townsville</li>
      </ul>
      <a class="btn">Get a Free Quote ↗</a>
    </div>
    <svg class="ph map" role="img" aria-label="Satellite map of the coast from Townsville to the Whitsundays with location markers" width="508" height="412"><defs><linearGradient id="mapG" x1="0" y1="0" x2="1" y2="0"><stop offset="0" stop-color="#4a4a32"/><stop offset=".55" stop-color="#3a4a38"/><stop offset="1" stop-color="#1c4a5e"/></linearGradient></defs><rect width="508" height="412" fill="url(#mapG)"/></svg>
  </div>
</section>

<section class="cta">
  <svg class="ph cta-photo" role="img" aria-label="Welder in protective helmet with bright sparks" width="560" height="485"><defs><radialGradient id="ctaG" cx=".45" cy=".55" r=".7"><stop offset="0" stop-color="#e08a3a"/><stop offset=".4" stop-color="#3e3a3e"/><stop offset="1" stop-color="#141a24"/></radialGradient><linearGradient id="ctaFade" x1="0" x2="1"><stop offset=".6" stop-color="#4f93c8" stop-opacity="0"/><stop offset="1" stop-color="#4f93c8"/></linearGradient></defs><rect width="560" height="485" fill="url(#ctaG)"/><rect width="560" height="485" fill="url(#ctaFade)"/></svg>
  <div class="cta-copy">
    <div class="eyebrow">Contact Us</div>
    <h2 class="display">Let's Build Some Incredible</h2>
    <p>Lorem ipsum dolor sit amet, consectetur adipiscing elit, sed do eiusmod tempor incididunt ut labore</p>
    <a class="btn btn-dark">Get a Free Quote ↗</a>
  </div>
</section>

<footer>
  <div class="foot-cols">
    <div class="foot-brand">
      <div class="brand"><span class="brand-mark"></span>Brightline Coatings Co</div>
      <p>Lorem ipsum dolor sit amet, consectetur adipiscing elit, sed do eiusmod tempor incididunt ut labore et dolore magna aliqua. Quis ipsum suspendisse ultrices gravida. Risus</p>
      <div class="socials"><span></span><span></span><span></span></div>
    </div>
    <div class="foot-col" style="width:155px"><h5>Navigation</h5><ul><li>Home</li><li>About Us</li><li>Services</li><li>Projects</li><li>Gallery</li><li>Contact</li></ul></div>
    <div class="foot-col" style="width:188px"><h5>Services</h5><ul><li>Handrails</li><li>Privacy Slat Screens</li><li>Electric Gates</li><li>Pool Fencing</li><li>Glass Balustrades</li><li>Stainless Steel Fabrication</li><li>Powder Coated Aluminium</li></ul></div>
    <div class="foot-col" style="width:178px"><h5>Area We Serve</h5><ul><li>Airlie Beach</li><li>Cannonvale</li><li>Proserpine</li><li>Bowen</li><li>Ayr</li><li>Home Hill</li><li>Townsville</li><li>Surrounding Areas</li></ul></div>
    <div class="foot-col" style="width:200px"><h5>Contact</h5>
      <div class="contact-row"><svg viewBox="0 0 24 24"><path d="M6.6 10.8a15.1 15.1 0 0 0 6.6 6.6l2.2-2.2a1 1 0 0 1 1-.25 11.4 11.4 0 0 0 3.6.57 1 1 0 0 1 1 1V20a1 1 0 0 1-1 1A17 17 0 0 1 3 4a1 1 0 0 1 1-1h3.5a1 1 0 0 1 1 1c0 1.25.2 2.45.57 3.6a1 1 0 0 1-.25 1z"/></svg>0400 000 111</div>
      <div class="contact-row"><svg viewBox="0 0 24 24"><path d="M2 5h20v14H2zM2 5l10 8 10-8" stroke="#0a2342" stroke-width="1.5"/></svg>info@brightlinecoatings.example</div>
      <div class="contact-row"><svg viewBox="0 0 24 24"><path d="M12 2a7 7 0 0 1 7 7c0 5-7 13-7 13S5 14 5 9a7 7 0 0 1 7-7z"/></svg>Whitsunday, QLD<br>Airlie Beach to Townsville</div>
    </div>
  </div>
  <div class="foot-bottom"><span>© 2025 Your Company . All Rights Reserved.</span><span>Privacy Policy | Terms &amp; Conditions | Sitemap</span></div>
</footer>

</body>
</html>
```